Telecommunications/Power civil contractor needs business card design

Were a new telecommunications/power underground civil contractor that is looking for a new business card design. Our company colours are silver or grey and orange. Feel free to use the white background logo or the black background logo.

Target Market(s)

Local contractors, utility companies, private sector mining/energy companies, developers.

Industry/Entity Type

Telecommunications

Contact Information for Business Card

Each card will need the following info:
Persons name:
Title:
E-mail:
Phone number:
Shop Address:
Mailing Address:

Requirements
Must have
• Each card will need the following info:
• Persons name:
• Title:
• E-mail:
• Phone number:
• Shop Address:
• Mailing Address:

```html
<!DOCTYPE html>
<html lang="en">
<head>
<meta charset="utf-8">
<title>Tandem Line Contracting Inc – Business Card</title>
<link rel="stylesheet" href="https://fonts.googleapis.com/css2?family=Source+Sans+3:wght@400;600;700&display=swap">
<style>
  :root {
    --orange: #f15a24;
    --grey-card: #d6d6d6;
    --grey-mark: #9a9a9a;
    --grey-rim: #6e6e6e;
    --grey-text: #6a6a6a;
    --white: #ffffff;
    --backdrop: #ececec;
  }
  html, body {
    margin: 0;
    padding: 0;
    width: 1200px;
    height: 900px;
    overflow: hidden;
    background: var(--backdrop);
    font-family: "Source Sans 3", Arial, sans-serif;
  }
  .canvas {
    position: relative;
    width: 1200px;
    height: 900px;
  }
  .card {
    position: absolute;
    overflow: hidden;
    box-shadow: 0 6px 18px rgba(0,0,0,0.18);
  }
  .card-front {
    left: 237px;
    top: 61px;
    width: 556px;
    height: 344px;
    background: var(--orange);
  }
  .card-back {
    left: 458px;
    top: 518px;
    width: 560px;
    height: 343px;
    background: var(--grey-card);
  }
  .front-disc {
    position: absolute;
    left: 0;
    top: 0;
  }
  .contact {
    position: absolute;
    left: 288px;
    top: 57px;
    color: var(--white);
  }
  .contact-name {
    margin: 0;
    font-size: 20px;
    font-weight: 700;
    line-height: 24px;
  }
  .contact-title {
    margin: 0 0 10px;
    font-size: 14.5px;
    font-weight: 400;
    line-height: 18px;
  }
  .contact-line {
    display: flex;
    align-items: center;
    gap: 8px;
    margin: 0;
    font-size: 15.5px;
    line-height: 20px;
  }
  .contact-line svg { flex: none; }
  .address-title {
    margin: 14px 0 0;
    font-size: 17.5px;
    font-weight: 600;
    line-height: 22px;
  }
  .address-title.mailing { margin-top: 6px; }
  .address-line {
    margin: 0;
    font-size: 15.5px;
    line-height: 20px;
  }
  .brand {
    position: absolute;
    left: 0;
    right: 0;
    top: 75px;
    text-align: center;
  }
  .brand-circle {
    display: block;
    margin: 0 auto 50px;
  }
  .brand-name {
    margin: 0;
    color: var(--orange);
    font-size: 32px;
    font-weight: 700;
    line-height: 32px;
    letter-spacing: 2px;
  }
  .brand-tagline {
    margin: 4px 0 0;
    color: var(--grey-text);
    font-size: 18px;
    font-weight: 700;
    line-height: 22px;
    letter-spacing: 2.5px;
  }
</style>
</head>
<body>
<main class="canvas">

  <section class="card card-front" aria-label="Business card front">
    <svg class="front-disc" width="260" height="344" viewBox="0 0 260 344" aria-hidden="true">
      <circle cx="62" cy="172" r="176" fill="var(--grey-rim)"/>
      <circle cx="58" cy="172" r="168" fill="var(--grey-mark)"/>
    </svg>

    <div class="contact">
      <p class="contact-name">Daniel Reyes</p>
      <p class="contact-title">Project Manager</p>
      <p class="contact-line">
        <svg width="12" height="12" viewBox="0 0 24 24" aria-hidden="true"><path fill="#fff" d="M6.6 10.8a15.1 15.1 0 0 0 6.6 6.6l2.2-2.2c.3-.3.7-.4 1-.2 1.1.4 2.3.6 3.6.6.6 0 1 .4 1 1V20c0 .6-.4 1-1 1A17 17 0 0 1 3 4c0-.6.4-1 1-1h3.5c.6 0 1 .4 1 1 0 1.3.2 2.5.6 3.6.1.3 0 .7-.2 1z"/></svg>
        044-123 456 789
      </p>
      <p class="contact-line">
        <svg width="12" height="10" viewBox="0 0 24 18" aria-hidden="true"><path fill="#fff" d="M0 0h24v18H0z"/><path fill="none" stroke="#f15a24" stroke-width="2" d="M1 1l11 8 11-8"/></svg>
        info@tandemline.com
      </p>

      <p class="address-title">Shop Address</p>
      <p class="address-line">12345, Address Goes Here</p>
      <p class="address-line">Country Name, 123456.</p>

      <p class="address-title mailing">Mailing Address</p>
      <p class="address-line">12345, Address Goes Here</p>
      <p class="address-line">Country Name, 123456.</p>
    </div>
  </section>

  <section class="card card-back" aria-label="Business card back">
    <div class="brand">
      <svg class="brand-circle" width="90" height="90" viewBox="0 0 90 90" aria-hidden="true">
        <circle cx="45" cy="45" r="41" fill="none" stroke="var(--orange)" stroke-width="6"/>
      </svg>
      <p class="brand-name">TANDEM LINE</p>
      <p class="brand-tagline">CONTRACTING INC</p>
    </div>
  </section>

</main>
</body>
</html>
```